The Brookhaven Sessions - Concert Series Website Design

I've recently decided to launch a concert series in my living room and would love a website to use to promote the series. I'm looking for a simple Wix design that I could take over once it's complete. I'll provide the logo for which I'd like the website to utilize the color scheme.

Target Market(s)

Music lovers in Denver

Industry/Entity Type

Music

Coding

Coded - Design and coding required

Number of Pages Required

2 page

Font styles to use
Script

Requirements
Must have
• 2 pages - one for concert goers to see the schedule and rsvp, and one for artists about the booking process

```html
<!DOCTYPE html>
<html lang="en">
<head>
<meta charset="utf-8">
<title>The Brookhaven Sessions</title>
<link href="https://fonts.googleapis.com/css2?family=DM+Sans:wght@500;600;700&family=Roboto:wght@400;500&display=swap" rel="stylesheet">
<style>
:root{
  --purple:#2b0a4c;
  --purple-deep:#1f0638;
  --purple-mid:#4a1c6e;
  --gold:#f7c26a;
  --gold-soft:#fbd58f;
  --cream:#fcf6d6;
  --ink:#1e1a22;
  --white:#ffffff;
}
*{box-sizing:border-box;margin:0;padding:0}
html,body{width:1200px;height:2851px;overflow:hidden}
body{font-family:"Roboto",sans-serif;color:var(--ink);background:var(--white);position:relative}
.abs{position:absolute}
h1,h2,h3,.heading{font-family:"DM Sans",sans-serif}

/* header */
.site-header{left:0;top:0;width:1200px;height:81px;background:var(--cream)}
.header-band{right:0;top:0;width:545px;height:81px;background:linear-gradient(90deg,#4a1458,#6a2a6a 60%,#5c2460);clip-path:polygon(44px 0,100% 0,100% 100%,0 100%)}
.brand{left:112px;top:20px;display:flex;align-items:center;gap:10px}
.brand-mark{width:34px;height:34px;border-radius:50%;background:var(--purple-mid)}
.brand-name{font-family:"DM Sans",sans-serif;font-weight:600;font-size:20px;color:var(--purple-mid);line-height:1.05;width:150px}
.nav{left:372px;top:31px;display:flex;gap:34px;font-size:15px;color:var(--purple)}
.nav a{color:inherit;text-decoration:none}
.nav .active{font-weight:500;border-bottom:2px solid var(--purple-mid);padding-bottom:4px}
.header-contact{left:727px;top:30px;display:flex;gap:38px;color:var(--white);font-size:15px}
.header-contact span{display:flex;align-items:center;gap:10px}

/* hero */
.hero{left:0;top:81px;width:1200px;height:568px;background:radial-gradient(ellipse at 30% 50%,#2a2a8a 0%,#1a1040 40%,#120824 75%),#120824}
.hero-copy{left:0;top:238px;width:1200px;text-align:center}
.hero-title{font-family:"DM Sans",sans-serif;font-weight:700;font-size:64px;line-height:1;color:var(--gold)}
.hero-sub{font-family:"DM Sans",sans-serif;font-weight:600;font-size:52px;line-height:1;color:var(--white);margin-top:8px}
.hero-text{color:var(--white);font-size:15px;margin-top:30px}
.btn{display:inline-flex;align-items:center;gap:12px;font-family:"DM Sans",sans-serif;font-weight:600;font-size:16px;padding:10px 15px;background:var(--gold);color:var(--purple);text-decoration:none}
.btn.outline{background:transparent;border:1px solid var(--gold);color:var(--gold)}
.btn .dot{width:16px;height:16px;border-radius:50%;background:var(--purple);display:inline-flex;align-items:center;justify-content:center}
.btn.outline .dot{background:var(--gold)}
.hero .btn{margin-top:40px}

/* features */
.features{left:110px;top:722px;width:980px;display:flex}
.feature{flex:1;text-align:center;height:152px;padding-top:0}
.feature+.feature{border-left:1px solid #9c8ab0}
.feature h3{font-size:21px;font-weight:600;color:var(--purple);margin-top:18px}
.feature p{font-size:15px;line-height:22px;margin-top:12px}

/* about */
.about-bg{left:0;top:1080px;width:1200px;height:750px;background:linear-gradient(180deg,#ffffff 0%,#d8d4d8 25%,#8f8496 60%,#6d6378 100%)}
.section-head{left:0;width:1200px;text-align:center}
.section-title{font-size:41px;font-weight:600;color:var(--purple)}
.section-title .note{color:var(--gold);font-size:32px}
.tags{display:flex;justify-content:center;gap:18px;margin-top:22px}
.tags span{background:var(--gold);color:var(--purple);font-size:15px;letter-spacing:3px;padding:1px 3px}
.about-text{left:300px;top:1085px;width:600px;text-align:center;font-size:15px;line-height:22px}
.about-text p+p{margin-top:16px}

/* sessions */
.sessions{left:112px;top:1372px;width:977px;height:754px;background:var(--purple)}
.sessions .section-title{color:var(--white)}
.sessions .tags{gap:8px}
.sessions .tags span{background:#5a3876;color:var(--gold-soft)}
.card{top:227px;width:265px;text-align:center;color:var(--white)}
.card-photo{width:265px;height:232px;background:linear-gradient(160deg,#6a1b4e 0%,#3a0f38 55%,#1c0620 100%);position:relative}
.card-name{position:absolute;left:0;right:0;bottom:14px;font-family:"DM Sans",sans-serif;font-weight:600;font-size:31px;color:var(--white)}
.card-date{color:var(--gold);font-size:13px;margin-top:24px}
.card h3{font-size:21px;font-weight:600;margin-top:6px}
.card p{font-size:15px;line-height:22px;margin-top:14px}
.card .btn{margin-top:26px;font-size:15px;padding:8px 14px}

/* rsvp */
.rsvp-bg{left:0;top:2126px;width:1200px;height:477px;background:var(--cream)}
.field{top:2375px;width:265px;height:61px;border:1px solid var(--purple-mid)}
.field label{position:absolute;left:18px;top:-10px;background:var(--cream);padding:0 5px;font-size:15px;color:var(--purple)}
.field .ph{position:absolute;left:22px;top:21px;font-size:14px;color:#5b5360}
.field .count{position:absolute;right:18px;top:20px;font-size:15px;color:var(--purple);display:flex;gap:16px;align-items:center}

/* footer */
.site-footer{left:0;top:2603px;width:1200px;height:248px;background:var(--purple)}
.foot-brand{left:112px;top:46px;display:flex;align-items:center;gap:22px}
.foot-brand .brand-mark{width:130px;height:130px;border-radius:14px;background:#7a3a6a}
.foot-brand .brand-name{font-size:46px;color:var(--cream);font-weight:500;width:320px;line-height:1}
.copyright{left:265px;top:192px;color:var(--white);font-size:13px}
.contact-title{left:727px;top:52px;color:var(--gold);font-size:18px;font-weight:500;font-family:"DM Sans",sans-serif}
.contact-row{left:727px;color:var(--white);font-size:15px;display:flex;gap:32px}
.contact-row span{display:flex;align-items:center;gap:12px}
.socials{left:729px;top:180px;display:flex;align-items:center;gap:12px;color:var(--white);font-family:"DM Sans",sans-serif;font-size:18px;font-weight:500}
.socials i{width:18px;height:18px;border-radius:50%;background:var(--gold);display:inline-block}
.socials i:first-of-type{margin-left:10px}
</style>
</head>
<body>

<header class="site-header abs">
  <div class="header-band abs"></div>
  <div class="brand abs"><span class="brand-mark"></span><span class="brand-name">The Brookhaven Sessions</span></div>
  <nav class="nav abs"><a class="active" href="#">Home</a><a href="#">About Artists</a><a href="#">Contact</a></nav>
  <div class="header-contact abs">
    <span><svg width="16" height="16" viewBox="0 0 24 24"><path d="M6.6 10.8a15 15 0 006.6 6.6l2.2-2.2a1 1 0 011-.25 11.4 11.4 0 003.6.6 1 1 0 011 1V20a1 1 0 01-1 1A17 17 0 013 4a1 1 0 011-1h3.5a1 1 0 011 1c0 1.25.2 2.45.6 3.6a1 1 0 01-.25 1z" fill="#f7c26a"/></svg>+(123) 555 0142</span>
    <span><svg width="18" height="14" viewBox="0 0 18 14"><rect width="18" height="14" rx="2" fill="#f7c26a"/><path d="M1 2l8 6 8-6" stroke="#4a1458" stroke-width="1.5" fill="none"/></svg>info@brookhavensessions.com</span>
  </div>
</header>

<section class="hero abs" role="img" aria-label="Band performing in a dim living room lit with purple and blue light"></section>
<div class="hero-copy abs">
  <h1 class="hero-title">Living Room Concerts</h1>
  <p class="hero-sub">Glowing with Denver's Finest Talent</p>
  <p class="hero-text">Experience acoustic magic in a cozy space. Denver's hidden gem for music lovers. Bring your own vibe.</p>
  <a class="btn" href="#">Claim Your Seats <span class="dot"><svg width="8" height="8" viewBox="0 0 8 8"><path d="M1 4h6M4 1l3 3-3 3" stroke="#f7c26a" stroke-width="1.4" fill="none"/></svg></span></a>
</div>

<section class="features abs">
  <div class="feature">
    <svg width="48" height="42" viewBox="0 0 48 42" fill="none" stroke="#2b0a4c" stroke-width="3"><path d="M4 36a22 22 0 0122-22M10 36a16 16 0 0116-16M16 36a10 10 0 0110-10"/><path d="M38 4v28"/><circle cx="33" cy="33" r="5" fill="#2b0a4c"/><path d="M38 4h7"/></svg>
    <h3>Acoustic Talent</h3>
    <p>Talented pop artists deliver<br>glowing 45-minute sessions.</p>
  </div>
  <div class="feature">
    <svg width="44" height="42" viewBox="0 0 44 42" fill="none" stroke="#2b0a4c" stroke-width="3"><path d="M4 18L22 3l18 15v20H4z"/><path d="M14 30a8 8 0 0116 0z"/></svg>
    <h3>Intimate Venue</h3>
    <p>Cozy Denver living room<br>hosts 25 lucky music lovers.</p>
  </div>
  <div class="feature">
    <svg width="46" height="42" viewBox="0 0 46 42" fill="none" stroke="#2b0a4c" stroke-width="3"><circle cx="21" cy="23" r="17"/><circle cx="15" cy="20" r="1.5" fill="#2b0a4c"/><circle cx="27" cy="20" r="1.5" fill="#2b0a4c"/><path d="M13 27a9 9 0 0016 0"/><path d="M38 10l-4-4a2.5 2.5 0 014-3 2.5 2.5 0 014 3z" fill="#2b0a4c" stroke-width="1"/></svg>
    <h3>Relaxed Vibes</h3>
    <p>Easy &amp; relaxed ticket booking<br>RSVP now to claim your seats.</p>
  </div>
</section>

<div class="about-bg abs" role="img" aria-label="Faded photo of a singer at a microphone with band members"></div>
<div class="section-head abs" style="top:944px">
  <h2 class="section-title"><span class="note">♩</span> About Brookhaven Sessions <span class="note">♩</span></h2>
  <div class="tags"><span>DENVER'S</span><span>SUNSET</span><span>GLOW</span><span>UNPLUGGED</span></div>
</div>
<div class="about-text abs">
  <p>The Brookhaven Sessions brings Denver's music scene into an intimate living room. Inspired by mountain sunsets, we host unplugged concerts for 25 fans.</p>
  <p>Launched in 2026, we're Denver's cozy secret for music lovers seeking authentic nights. BYOB vibes foster connection; No tickets, just RSVP magic. Join the glow.</p>
  <div style="margin-top:52px"><a class="btn" href="#">Learn More About Us <span class="dot"><svg width="8" height="8" viewBox="0 0 8 8"><path d="M1 4h6M4 1l3 3-3 3" stroke="#f7c26a" stroke-width="1.4" fill="none"/></svg></span></a></div>
</div>

<section class="sessions abs">
  <div class="section-head abs" style="top:70px;width:977px">
    <h2 class="section-title"><span class="note">♩</span>Upcoming Sessions <span class="note">♩</span></h2>
    <div class="tags"><span>ALWAYS</span><span>KEEPING</span><span>THE</span><span>CONCERT</span><span>VIBES</span><span>TURNED-ON</span></div>
  </div>
  <article class="card abs" style="left:58px">
    <div class="card-photo" role="img" aria-label="Singer with guitar on a dim stage"><span class="card-name">ROWAN PIKE</span></div>
    <p class="card-date">Fri, Mar 13,2026 &nbsp;9.00 PM</p>
    <h3>Soulful Acoustic Groove</h3>
    <p>The graceful and smooth velvet<br>voice meets the guitar. magic.</p>
    <a class="btn outline" href="#">RSVP Now <span class="dot"><svg width="8" height="8" viewBox="0 0 8 8"><path d="M1 4h6M4 1l3 3-3 3" stroke="#2b0a4c" stroke-width="1.4" fill="none"/></svg></span></a>
  </article>
  <article class="card abs" style="left:355px">
    <div class="card-photo" role="img" aria-label="Vocalist singing into a microphone" style="border:1px solid #f7c26a"><span class="card-name">MIRA SOL</span></div>
    <p class="card-date">Sat, Mar 14,2026 &nbsp;7.30 PM</p>
    <h3>Indie Folk Whisperer</h3>
    <p>Soulful heart melting melodies<br>from the rising stars of Denver.</p>
    <a class="btn" href="#">RSVP Now <span class="dot"><svg width="8" height="8" viewBox="0 0 8 8"><path d="M1 4h6M4 1l3 3-3 3" stroke="#f7c26a" stroke-width="1.4" fill="none"/></svg></span></a>
  </article>
  <article class="card abs" style="left:652px">
    <div class="card-photo" role="img" aria-label="Singer and saxophone player performing"><span class="card-name">ELLIS REED</span></div>
    <p class="card-date">Mon, Mar 16,2026 &nbsp;8.30 PM</p>
    <h3>Mountain Indie Poet</h3>
    <p>Raw lyrics in a cozy glow from<br>the peak mountains of Denver.</p>
    <a class="btn outline" href="#">RSVP Now <span class="dot"><svg width="8" height="8" viewBox="0 0 8 8"><path d="M1 4h6M4 1l3 3-3 3" stroke="#2b0a4c" stroke-width="1.4" fill="none"/></svg></span></a>
  </article>
</section>

<div class="rsvp-bg abs"></div>
<div class="section-head abs" style="top:2205px">
  <h2 class="section-title"><span class="note">♩</span> RSVP for the Glow <span class="note">♩</span></h2>
  <div class="tags" style="gap:14px"><span>SECURE</span><span>YOUR</span><span>INTIMATE</span><span>SEATS</span><span>TODAY</span></div>
</div>
<div class="field abs" style="left:170px"><label>Your Name</label><span class="ph">Full Name...</span></div>
<div class="field abs" style="left:467px"><label>Your Email</label><span class="ph">Email Address...</span></div>
<div class="field abs" style="left:764px"><label>Guest Count</label><span class="ph">No.of Guests...</span><span class="count"><small>◂</small>4<small>▸</small></span></div>
<div class="abs" style="left:0;top:2476px;width:1200px;text-align:center">
  <a class="btn" href="#">Submit RSVP <span class="dot"><svg width="8" height="8" viewBox="0 0 8 8"><path d="M1 4h6M4 1l3 3-3 3" stroke="#f7c26a" stroke-width="1.4" fill="none"/></svg></span></a>
</div>

<footer class="site-footer abs">
  <div class="foot-brand abs"><span class="brand-mark"></span><span class="brand-name">The Brookhaven Sessions</span></div>
  <p class="copyright abs">© 2026 The Brookhaven Sessions.All Rights Reserved.</p>
  <h3 class="contact-title abs">Contact Information</h3>
  <div class="contact-row abs" style="top:104px">
    <span><svg width="16" height="16" viewBox="0 0 24 24"><path d="M6.6 10.8a15 15 0 006.6 6.6l2.2-2.2a1 1 0 011-.25 11.4 11.4 0 003.6.6 1 1 0 011 1V20a1 1 0 01-1 1A17 17 0 013 4a1 1 0 011-1h3.5a1 1 0 011 1c0 1.25.2 2.45.6 3.6a1 1 0 01-.25 1z" fill="#f7c26a"/></svg>+(123) 555 0142</span>
    <span><svg width="18" height="14" viewBox="0 0 18 14"><rect width="18" height="14" rx="2" fill="#f7c26a"/><path d="M1 2l8 6 8-6" stroke="#2b0a4c" stroke-width="1.5" fill="none"/></svg>info@brookhavensessions.com</span>
  </div>
  <div class="contact-row abs" style="top:140px">
    <span><svg width="14" height="18" viewBox="0 0 14 18"><path d="M7 0a7 7 0 00-7 7c0 5 7 11 7 11s7-6 7-11a7 7 0 00-7-7z" fill="#f7c26a"/><circle cx="7" cy="7" r="2.5" fill="#2b0a4c"/></svg>2417 Larkspur Ave, Denver, CO 80206</span>
  </div>
  <div class="socials abs">Follow Our Socials <i></i><i></i><i></i><i></i></div>
</footer>

</body>
</html>
```